co working space / serviced office/ business centre

Brevlo - brevlo.in, is a very young brand bieng run by 3 young entrepreneurs. We want to be become out of the league company delivering fabulous and beautiful serviced offices in India and abroad. We hire designers who have made spaces across the world. We want to get visiting card design which gives complete fresh look to the people who carries that card, has to be very impactful and should symbolise happy young and energetic brand. should be completely out of the box thinking of international level, should portray global brand image.

Target Market(s)

Startups, (Small, medium and large corporates)

Industry/Entity Type

Business

Contact Information for Business Card

Name, Email, Address, Mobile number, Landline number, website

Colors

Designer to choose colors to be used in the design.

Requirements
Must have
• Nice new shape
Nice to have
• We want creative cuts, different size and impactful brand clarity
Should not have
• Boring and regular design and shape

```html
<!DOCTYPE html>
<html lang="en">
<head>
<meta charset="utf-8">
<title>Brevlo Business Card</title>
<link rel="stylesheet" href="https://fonts.googleapis.com/css2?family=Open+Sans:wght@400;600;700&display=swap">
<style>
  :root {
    --brand-red: #ed1c24;
    --card-grey: #dcdfdd;
    --ink: #2b2b2b;
    --white: #ffffff;
    --stage-dark: #111111;
    --stage-light: #4e4e4e;
  }
  html, body {
    margin: 0;
    padding: 0;
    width: 1200px;
    height: 900px;
    overflow: hidden;
  }
  .stage {
    position: relative;
    width: 1200px;
    height: 900px;
    background: linear-gradient(135deg, var(--stage-dark) 0%, var(--stage-light) 50%, var(--stage-dark) 100%);
    font-family: "Open Sans", Arial, sans-serif;
  }
  .card-shape {
    position: absolute;
    top: 255px;
    width: 475px;
    height: 323px;
  }
  .card-front { left: 100px; }
  .card-back { left: 618px; }

  .brand {
    position: absolute;
    width: 260px;
    text-align: center;
  }
  .brand-name {
    margin: 0;
    font-size: 36px;
    font-weight: 700;
    letter-spacing: 3px;
    line-height: 1;
  }
  .brand-rule {
    height: 2px;
    margin: 6px 30px 7px;
  }
  .brand-tagline {
    margin: 0;
    font-size: 11px;
    font-weight: 600;
    letter-spacing: 2.5px;
    line-height: 14px;
  }
  .brand-front { left: 207px; top: 379px; }
  .brand-front .brand-name,
  .brand-front .brand-tagline { color: var(--brand-red); }
  .brand-front .brand-rule { background: var(--brand-red); }

  .brand-back { left: 725px; top: 459px; }
  .brand-back .brand-name,
  .brand-back .brand-tagline { color: var(--white); }
  .brand-back .brand-rule { background: var(--white); }

  .person {
    position: absolute;
    right: 878px;
    top: 471px;
    text-align: right;
    color: var(--ink);
    font-size: 13px;
    line-height: 19px;
  }
  .person p { margin: 0; }
  .person .person-name {
    color: var(--brand-red);
    font-size: 15px;
    font-weight: 600;
    letter-spacing: 0.5px;
  }
  .person .person-role { margin-bottom: 2px; }

  .divider {
    position: absolute;
    left: 338px;
    top: 478px;
    width: 1px;
    height: 60px;
    background: var(--brand-red);
  }
  .contact-list {
    position: absolute;
    left: 354px;
    top: 473px;
    margin: 0;
    padding: 0;
    list-style: none;
    color: var(--ink);
    font-size: 13px;
    line-height: 17.5px;
  }
  .contact-list li {
    display: flex;
    align-items: center;
    gap: 6px;
  }
  .contact-icon {
    width: 11px;
    height: 11px;
    fill: var(--brand-red);
    flex: none;
  }
</style>
</head>
<body>
<main class="stage">
  <svg class="card-shape card-front" viewBox="0 0 475 323" aria-hidden="true">
    <path fill="var(--card-grey)" d="M0,110 Q80,78 170,67 C170,22 205,0 237,0 C270,0 305,22 305,67 Q400,78 475,108 L475,311 Q475,323 463,323 L12,323 Q0,323 0,311 Z"/>
  </svg>
  <svg class="card-shape card-back" viewBox="0 0 475 323" aria-hidden="true">
    <path fill="var(--brand-red)" d="M0,110 Q80,78 170,67 C170,22 205,0 237,0 C270,0 305,22 305,67 Q400,78 475,108 L475,311 Q475,323 463,323 L12,323 Q0,323 0,311 Z"/>
  </svg>

  <div class="brand brand-front">
    <h1 class="brand-name">BREVLO</h1>
    <div class="brand-rule"></div>
    <p class="brand-tagline">PLAN. MEET. GROW</p>
  </div>

  <div class="person">
    <p class="person-name">ARJUN MEHTA</p>
    <p class="person-role">Managing Director</p>
    <p>12345, Address Goes Here</p>
    <p>Country Name, 123456.</p>
  </div>

  <div class="divider"></div>

  <ul class="contact-list">
    <li>
      <svg class="contact-icon" viewBox="0 0 12 12"><path d="M3,0 H9 Q10,0 10,1 V11 Q10,12 9,12 H3 Q2,12 2,11 V1 Q2,0 3,0 Z M3.5,1.5 V9.5 H8.5 V1.5 Z"/></svg>
      044-123 456 789
    </li>
    <li>
      <svg class="contact-icon" viewBox="0 0 12 12"><path d="M0,4 Q6,0 12,4 L11,6 L8.5,5 V4 Q6,3 3.5,4 V5 L1,6 Z M2,7 H10 V11 H2 Z"/></svg>
      044-123 456 789
    </li>
    <li>
      <svg class="contact-icon" viewBox="0 0 12 12"><path d="M0,2 H12 V10 H0 Z"/><path d="M0.5,2.5 L6,7 L11.5,2.5" stroke="var(--card-grey)" stroke-width="1.2" fill="none"/></svg>
      info@webname.com
    </li>
    <li>
      <svg class="contact-icon" viewBox="0 0 12 12"><circle cx="6" cy="6" r="5.5"/><path d="M1,6 H11 M6,0.5 Q3,6 6,11.5 M6,0.5 Q9,6 6,11.5" stroke="var(--card-grey)" stroke-width="0.8" fill="none"/></svg>
      www.websitename.com
    </li>
  </ul>

  <div class="brand brand-back">
    <h2 class="brand-name">BREVLO</h2>
    <div class="brand-rule"></div>
    <p class="brand-tagline">PLAN. MEET. GROW</p>
  </div>
</main>
</body>
</html>
```